Harborview Estates Business Card for Apartment Buildings

Create business cards for resident managers who run apartment buildings. The audience is the public who are searching for apartment rentals, and current residents who live at the apartment building. Key design element will be incorporating the company logo, however, the logo cannot dominate. The building name and manager name are more important than the logo. Current business card design leaves little room for copy, so we may need to reduce the size on the current card to allow for more space for copy.

Target Market(s)

Adults 18-65 years of age, who are looking for an apartment rental, plus current residents who live at our apartment buildings.

Industry/Entity Type

Property Management

Contact Information for Business Card

A major design element will be use of the company logo. Important property and manager contact information must be part of the design. The size of the logo will need to be reduced to make room for building and manager contact copy.

Font styles to use
Sans Serif

Colors
3176b5
000000
959595
ffffff

Requirements
Must have
• 1) Incorporate the company logo.
• 2) Use the company colors (dark blue, black/grey, over white).
• 3) FEATURE THE BUILDING NAME
• 4) FEATURE THE MANAGER NAME
• 5) The company name is less important than BUILDING and MANAGER
• 6) Manager contact information
• **SEE ATTACHED CREATIVE BRIEF**
Nice to have
• 1) Back of card logo watermark
• 2) Ability to write notes on back of carfd
Should not have
• Avoid letting the company logo dominate the card, the building name and manager are more important than the company logo.

```html
<!DOCTYPE html>
<html lang="en">
<head>
<meta charset="utf-8">
<title>Harborview Estates – Business Card</title>
<link rel="stylesheet" href="https://fonts.googleapis.com/css2?family=Hind:wght@400;600&family=Arimo:wght@400&display=swap">
<style>
  :root {
    --brand-blue: #1a6aab;
    --ink-dark: #404042;
    --ink-grey: #5f5f61;
    --rule-grey: #959595;
    --stage: #9a9a9a;
    --card-white: #ffffff;
    --card-back: #e3e4e4;
    --band-text: #ffffff;
  }
  * { margin: 0; padding: 0; box-sizing: border-box; }
  html, body { width: 1200px; height: 1200px; overflow: hidden; }
  body { background: var(--stage); position: relative; font-family: "Hind", Arial, sans-serif; }

  .card { position: absolute; left: 206px; width: 790px; height: 450px; }
  .card-front { top: 94px; background: var(--card-white); }
  .card-back { top: 656px; background: var(--card-back); }

  /* company line (front) – kept modest */
  .company-lockup {
    position: absolute; top: 84px; left: 0; width: 100%;
    display: flex; align-items: center; justify-content: center; gap: 12px;
  }
  .company-mark { width: 22px; height: 22px; background: var(--brand-blue); flex: none; }
  .company-name {
    font-weight: 600; font-size: 22px; line-height: 1; letter-spacing: 2px;
    color: var(--ink-dark); text-transform: uppercase; padding-top: 4px;
  }

  /* building name – featured */
  .building-name {
    position: absolute; top: 124px; left: 0; width: 100%; text-align: center;
    font-weight: 600; font-size: 38px; line-height: 1.1; letter-spacing: 1px;
    color: var(--brand-blue); text-transform: uppercase;
  }

  /* manager block */
  .manager { position: absolute; right: 425px; top: 212px; text-align: right; }
  .manager-name {
    font-weight: 600; font-size: 28px; color: var(--brand-blue); line-height: 1.2;
    margin-bottom: 2px;
  }
  .manager-role, .manager-address {
    font-weight: 400; font-size: 18px; line-height: 25px; color: var(--ink-grey);
  }
  .divider {
    position: absolute; left: 394px; top: 216px; width: 1.5px; height: 112px;
    background: var(--rule-grey);
  }

  .contact-list { position: absolute; left: 418px; top: 218px; list-style: none; }
  .contact-item {
    display: flex; align-items: center; gap: 12px; height: 28px;
    font-size: 18px; color: var(--ink-grey);
  }
  .contact-icon { width: 17px; height: 17px; fill: var(--brand-blue); flex: none; }

  /* back */
  .back-lockup {
    position: absolute; top: 180px; left: 0; width: 100%;
    display: flex; align-items: center; justify-content: center; gap: 16px;
  }
  .back-lockup .company-mark { width: 36px; height: 36px; }
  .back-lockup .company-name { font-size: 34px; color: var(--ink-dark); letter-spacing: 2px; }

  .back-band {
    position: absolute; left: 0; bottom: 0; width: 100%; height: 43px;
    background: var(--brand-blue);
    display: flex; align-items: center; justify-content: center;
    font-family: "Arimo", Arial, sans-serif; font-size: 17px; letter-spacing: 1.3px;
    color: var(--band-text);
  }
  .band-sep { margin: 0 14px; }
</style>
</head>
<body>

<section class="card card-front">
  <div class="company-lockup">
    <span class="company-mark"></span>
    <span class="company-name">Harborview Estates LLC</span>
  </div>
  <div class="building-name">Cedar Crest Apartments</div>

  <div class="manager">
    <div class="manager-name">Marisol Vega</div>
    <div class="manager-role">Resident Manager</div>
    <div class="manager-address">2845 Linden Avenue San<br>Diego, CA 92116</div>
  </div>

  <div class="divider"></div>

  <ul class="contact-list">
    <li class="contact-item">
      <svg class="contact-icon" viewBox="0 0 24 24" aria-hidden="true"><path d="M6.6 10.8c1.4 2.8 3.8 5.1 6.6 6.6l2.2-2.2c.3-.3.7-.4 1-.2 1.1.4 2.3.6 3.6.6.6 0 1 .4 1 1V20c0 .6-.4 1-1 1C10.6 21 3 13.4 3 4c0-.6.4-1 1-1h3.5c.6 0 1 .4 1 1 0 1.3.2 2.5.6 3.6.1.3 0 .7-.2 1z"/></svg>
      <span>619-555-0142</span>
    </li>
    <li class="contact-item">
      <svg class="contact-icon" viewBox="0 0 24 24" aria-hidden="true"><path d="M6 2h12v5H6zM4 8h16c1.1 0 2 .9 2 2v7h-4v5H6v-5H2v-7c0-1.1.9-2 2-2zm4 8v4h8v-4z"/></svg>
      <span>619-555-0187</span>
    </li>
    <li class="contact-item">
      <svg class="contact-icon" viewBox="0 0 24 24" aria-hidden="true"><path d="M7 1h10c1.1 0 2 .9 2 2v18c0 1.1-.9 2-2 2H7c-1.1 0-2-.9-2-2V3c0-1.1.9-2 2-2zm0 3v15h10V4zm5 16.2a1 1 0 1 0 0 .1z"/></svg>
      <span>619-555-0123</span>
    </li>
    <li class="contact-item">
      <svg class="contact-icon" viewBox="0 0 24 24" aria-hidden="true"><path d="M2 5h20v14H2zm2 2v.4l8 5.6 8-5.6V7zm0 2.8V17h16V9.8l-8 5.6z"/></svg>
      <span>marisol@harborviewest.com</span>
    </li>
  </ul>
</section>

<section class="card card-back">
  <div class="back-lockup">
    <span class="company-mark"></span>
    <span class="company-name">Harborview Estates</span>
  </div>
  <div class="back-band">
    <span>Cedar Crest Apartments</span><span class="band-sep">\</span><span>www.harborviewestates.us</span>
  </div>
</section>

</body>
</html>
```